Fire Risk Assessment App needs a sleek UI design

I need a sleek, modern but professional design for my 5 page Fire Risk Assessment App. Include gradient background, fire themed colours including reds, yellows, light orange and a touch of black. Design must ooze simplicity and professionalism. This is for the UK market. See attached images and word doc for more information.

Target Market(s)

General public and business owners

Industry/Entity Type

Technology / Fire Safety

Colors
00AB8E
00BBA5
67D7C9
C6EFE9
E9F9F6
59FF00
82FF00
B8FF75
E3FFCB
F4FFEA
FFC000
F8CF3A
FAE287
FDF2CF
FEFAEE
F0912C
F2A743
F7CA91
FBE8D2
FDF5EE
EE7325
F08F49
F5BC92
FAE3D3
FDF4ED
EB3D1F
EC4F4E
F09395
F8D3D4
FCEDEE

```html
<!DOCTYPE html>
<html lang="en">
<head>
<meta charset="utf-8">
<title>Fire Risk Assessment App – Screens</title>
<link href="https://fonts.googleapis.com/css2?family=Montserrat:wght@500;600;700&family=Lato:wght@400&display=swap" rel="stylesheet">
<style>
:root{
  --bg:#F2A743;
  --screen-top:#FDF5EE;
  --screen-bottom:#FBE8D2;
  --red:#EB3D1F;
  --red-bright:#EC2A2F;
  --ink:#1E1E1E;
  --muted:#6E6E6E;
  --green:#17B52D;
  --orange:#F0912C;
  --line:#BDBDBD;
  --white:#FFFFFF;
}
*{box-sizing:border-box;margin:0;padding:0}
html,body{width:1200px;height:789px;overflow:hidden}
body{background:var(--bg);font-family:'Montserrat',sans-serif;color:var(--ink);position:relative}
.screen{position:absolute;top:69px;width:302px;height:653px;border-radius:30px;overflow:hidden;
  background:linear-gradient(180deg,var(--screen-top) 0%,var(--screen-bottom) 100%)}
.screen--welcome{left:55px;background:linear-gradient(180deg,#FDF5EE 0%,#F7E2CB 55%,#FBE8D2 100%)}
.screen--dashboard{left:449px}
.screen--support{left:843px}
.abs{position:absolute}
.status{top:10px;left:0;right:0;height:14px;font-size:11px;font-weight:600}
.status .time{position:absolute;left:26px}
.status svg{position:absolute;right:24px;top:1px}
.center{left:0;right:0;text-align:center}
.headline{top:38px;font-size:15.5px;font-weight:600;line-height:24px}
.doc-art{left:49px;top:106px;width:202px;height:176px;border-radius:6px;
  background:linear-gradient(135deg,#FFFFFF,#F7CA91)}
.tagline{top:304px;font-size:15.5px;font-weight:600;line-height:24px}
.pill{left:42px;width:215px;height:45px;border-radius:23px;background:var(--red-bright);color:var(--white);
  font-size:13px;font-weight:700;display:flex;align-items:center}
.pill .ico{width:37px;height:37px;border-radius:50%;background:var(--white);margin-left:4px;margin-right:16px;display:flex;align-items:center;justify-content:center}
.pill--signup{top:366px}
.pill--login{top:475px}
.pill--login .ico{margin-right:22px}
.responsible{top:436px;font-size:15px;font-weight:600}
.endorsed{top:551px;font-size:12px;font-weight:500}
.fingerprint{left:125px;top:578px;width:48px;height:48px;border-radius:50%;background:var(--white);box-shadow:0 2px 6px rgba(0,0,0,.15);display:flex;align-items:center;justify-content:center}
.title{font-size:19.5px;font-weight:700}
.gauge{width:28px;height:28px;border-radius:50%;background:var(--white);box-shadow:0 1px 4px rgba(0,0,0,.2)}
.start{top:96px;font-size:13px;font-weight:600}
.add{left:122px;top:120px;width:58px;height:58px;border-radius:50%;background:var(--red-bright)}
.type-art{width:56px;height:56px;border-radius:50%;background:linear-gradient(135deg,#FFFFFF,#C9D6E3);box-shadow:0 2px 6px rgba(0,0,0,.12)}
.type-label{font-size:13px;font-weight:600;width:120px;text-align:center}
.chip{left:12px;width:123px;height:33px;background:var(--white);border-radius:3px;box-shadow:0 1px 4px rgba(0,0,0,.12);
  font-size:12px;font-weight:600;display:flex;align-items:center;justify-content:space-between;padding:0 5px 0 14px}
.chip .mark{width:30px;height:25px;background:#F3F3F3;display:flex;align-items:center;justify-content:center}
.item{left:14px;font-size:8px;font-weight:500;display:flex;align-items:center;gap:10px;text-transform:uppercase}
.item .thumb{width:14px;height:13px;border-radius:2px;background:linear-gradient(135deg,#DCE4EC,#9AA8B6)}
.item .thumb--home{background:linear-gradient(135deg,#F5BC92,#C95A3A)}
.navbar{left:0;right:0;bottom:0;height:44px;background:var(--white);display:flex;justify-content:space-around;align-items:center;padding:0 14px}
.prompt{left:25px;top:133px;font-family:'Lato',sans-serif;font-size:13px;color:var(--muted)}
.mic{left:238px;top:122px;width:35px;height:35px;border-radius:50%;background:var(--red-bright);display:flex;align-items:center;justify-content:center}
.reply{left:22px;top:167px;width:259px;height:179px;border:1px solid var(--line)}
.send{left:219px;top:359px;width:62px;height:33px;border:1.5px solid var(--red-bright);border-radius:3px;color:var(--red-bright);font-size:13px;font-weight:600;display:flex;align-items:center;justify-content:center;background:transparent}
</style>
</head>
<body>

<svg width="0" height="0" style="position:absolute">
  <defs>
    <symbol id="status-icons" viewBox="0 0 58 12">
      <rect x="0" y="8" width="2.5" height="4" fill="#1E1E1E"/><rect x="4" y="6" width="2.5" height="6" fill="#1E1E1E"/><rect x="8" y="3" width="2.5" height="9" fill="#1E1E1E"/><rect x="12" y="0" width="2.5" height="12" fill="#1E1E1E"/>
      <path d="M20 4a10 10 0 0 1 14 0l-2 2a7 7 0 0 0-10 0zM23 7a5.5 5.5 0 0 1 8 0l-4 4z" fill="#1E1E1E"/>
      <rect x="38" y="1.5" width="18" height="9" rx="2" fill="#1E1E1E"/><rect x="56.5" y="4" width="1.5" height="4" fill="#1E1E1E"/>
    </symbol>
    <symbol id="gauge" viewBox="0 0 28 28">
      <circle cx="14" cy="14" r="12" fill="#fff" stroke="#333" stroke-width="1.5"/>
      <path d="M6 16a8 8 0 0 1 4-8" stroke="#EB3D1F" stroke-width="2.5" fill="none"/>
      <path d="M10 8a8 8 0 0 1 8 0" stroke="#17B52D" stroke-width="2.5" fill="none"/>
      <path d="M18 8a8 8 0 0 1 4 8" stroke="#EB3D1F" stroke-width="2.5" fill="none"/>
      <path d="M14 15l-3-6" stroke="#333" stroke-width="1.8"/><circle cx="14" cy="15" r="2" fill="#333"/>
    </symbol>
    <symbol id="nav-icons-set" viewBox="0 0 0 0"></symbol>
  </defs>
</svg>

<!-- Welcome screen -->
<section class="screen screen--welcome">
  <div class="abs status"><span class="time">9:30</span><svg width="56" height="12"><use href="#status-icons"/></svg></div>
  <h1 class="abs center headline">The most user friendly' Fire Risk<br>Assessment App available. Market</h1>
  <div class="abs doc-art" role="img" aria-label="Illustration of fanned fire risk assessment question cards with a Photo button"></div>
  <p class="abs center tagline">Quick tap responses and voice<br>activated typing</p>
  <a class="abs pill pill--signup"><span class="ico">
    <svg width="20" height="20" viewBox="0 0 20 20" fill="none" stroke="#EC2A2F" stroke-width="1.5"><circle cx="9" cy="6" r="4"/><path d="M2 18c0-4 3-6 7-6 1.5 0 3 .4 4 1"/><path d="M16 12v6M13 15h6"/></svg>
  </span>Create a Free account</a>
  <p class="abs center responsible">Any Responsible Person can do it.</p>
  <a class="abs pill pill--login"><span class="ico">
    <svg width="20" height="20" viewBox="0 0 20 20" fill="none" stroke="#EC2A2F" stroke-width="1.5"><circle cx="8" cy="6" r="4"/><path d="M1 18c0-4 3-6 7-6 1 0 2 .2 3 .5"/><rect x="12" y="13" width="7" height="5" rx="1"/><path d="M13.5 13v-1.5a2 2 0 0 1 4 0V13"/></svg>
  </span>Customer Log in</a>
  <p class="abs center endorsed">Created and endorsed by british firefighters</p>
  <div class="abs fingerprint">
    <svg width="34" height="34" viewBox="0 0 34 34" fill="none" stroke="#333" stroke-width="1.3">
      <circle cx="17" cy="17" r="14"/><circle cx="17" cy="17" r="11"/><circle cx="17" cy="17" r="8"/><circle cx="17" cy="17" r="5"/><circle cx="17" cy="17" r="2"/>
    </svg>
  </div>
</section>

<!-- Dashboard screen -->
<section class="screen screen--dashboard">
  <div class="abs status"><span class="time">9:30</span><svg width="56" height="12"><use href="#status-icons"/></svg></div>
  <svg class="abs" style="left:38px;top:51px" width="28" height="28"><use href="#gauge"/></svg>
  <h1 class="abs title" style="left:84px;top:51px">DASHBOARD</h1>
  <p class="abs center start">Start Fire Risk Assessment</p>
  <div class="abs add"><svg width="58" height="58"><path d="M29 14v30M14 29h30" stroke="#fff" stroke-width="6"/></svg></div>
  <svg class="abs" style="left:0;top:0" width="302" height="300"><path d="M132 170L104 204M170 170L198 204" stroke="#333" stroke-width="1.5" stroke-dasharray="2 3"/></svg>
  <div class="abs type-art" style="left:66px;top:213px" role="img" aria-label="Commercial office building illustration"></div>
  <div class="abs type-art" style="left:181px;top:213px" role="img" aria-label="Residential house illustration"></div>
  <p class="abs type-label" style="left:34px;top:279px">Commercial</p>
  <p class="abs type-label" style="left:149px;top:279px">Residential</p>

  <div class="abs chip" style="top:320px">Complete<span class="mark"><svg width="18" height="18"><circle cx="9" cy="9" r="8" fill="#17B52D"/><path d="M5 9l3 3 5-6" stroke="#fff" stroke-width="2" fill="none"/></svg></span></div>
  <p class="abs item" style="top:368px"><span class="thumb" role="img" aria-label="Building thumbnail"></span>Reed's Barbershop</p>
  <div class="abs chip" style="top:399px">In Progress<span class="mark"><svg width="22" height="22"><circle cx="11" cy="11" r="9" stroke="#17B52D" stroke-width="1.8" fill="none"/></svg></span></div>
  <p class="abs item" style="top:447px"><span class="thumb" role="img" aria-label="Building thumbnail"></span>Elm Rd School</p>
  <p class="abs item" style="top:467px"><span class="thumb" role="img" aria-label="Building thumbnail"></span>St Anne's Care Home</p>
  <div class="abs chip" style="top:492px">Purchases<span class="mark"><svg width="18" height="18" fill="none" stroke="#17B52D" stroke-width="1.4"><path d="M3 6h12l-1 10H4z"/><path d="M6 6V4a3 3 0 0 1 6 0v2"/><path d="M7 11l2 2 3-3"/></svg></span></div>
  <p class="abs item" style="top:541px"><span class="thumb thumb--home" role="img" aria-label="House thumbnail"></span>Residential Fire Risk Assessment</p>
  <p class="abs item" style="top:561px"><span class="thumb" role="img" aria-label="Building thumbnail"></span>Commercial Fire Risk Assessment</p>
  <p class="abs item" style="top:580px"><span class="thumb" role="img" aria-label="Building thumbnail"></span>Commercial Fire Risk Assessment</p>

  <nav class="abs navbar">
    <svg width="28" height="28"><use href="#gauge"/></svg>
    <svg width="26" height="18"><rect x="1" y="2" width="24" height="14" rx="2" fill="#555"/><rect x="1" y="6" width="24" height="3" fill="#fff"/></svg>
    <svg width="24" height="22"><path d="M1 1h22v14H9l-6 5v-5H1z" fill="#555"/><path d="M5 6h14M5 10h10" stroke="#fff" stroke-width="1.5"/></svg>
    <svg width="22" height="26" fill="none" stroke="#555" stroke-width="2"><circle cx="13" cy="3.5" r="2.5" fill="#555"/><path d="M12 8l-3 8 5 3-1 6M9 16l-5 8M11 9l6 4 3-2M10 9l-4 3"/></svg>
  </nav>
</section>

<!-- Technical support screen -->
<section class="screen screen--support">
  <div class="abs status"><span class="time">9:30</span><svg width="56" height="12"><use href="#status-icons"/></svg></div>
  <svg class="abs" style="left:24px;top:70px" width="28" height="28"><path d="M2 2h24v18H10l-6 6v-6H2z" fill="#F0912C"/><path d="M7 9h14M7 14h10" stroke="#fff" stroke-width="2"/></svg>
  <h1 class="abs title" style="left:61px;top:70px">Technical Support</h1>
  <p class="abs prompt">Type / record you response here.</p>
  <div class="abs mic"><svg width="18" height="22" fill="none" stroke="#fff" stroke-width="1.8"><rect x="5" y="1" width="8" height="13" rx="4" fill="#fff"/><path d="M2 10a7 7 0 0 0 14 0M9 17v4"/></svg></div>
  <div class="abs reply"></div>
  <button class="abs send">Send</button>

  <nav class="abs navbar">
    <svg width="28" height="28"><use href="#gauge"/></svg>
    <svg width="26" height="18"><rect x="1" y="2" width="24" height="14" rx="2" fill="#555"/><rect x="1" y="6" width="24" height="3" fill="#fff"/></svg>
    <svg width="24" height="22"><path d="M1 1h22v14H9l-6 5v-5H1z" fill="#555"/><path d="M5 6h14M5 10h10" stroke="#fff" stroke-width="1.5"/></svg>
    <svg width="22" height="26" fill="none" stroke="#555" stroke-width="2"><circle cx="13" cy="3.5" r="2.5" fill="#555"/><path d="M12 8l-3 8 5 3-1 6M9 16l-5 8M11 9l6 4 3-2M10 9l-4 3"/></svg>
  </nav>
</section>

</body>
</html>
```